Business Card, A4 Letter Head and DL Envelope for Brandvelle

We are looking for a design for our Business Card, A4 Letter Head and DL Envelope.

Brandvelle is a distributor of promotional products. We specialize in a range of branded promotional products, these include pens, polo shirts, key rings, drink bottles, uniforms and bags to name a few. We are experts in marketing and assist companies in choosing the right promotional product for their needs. We will predominately be an online business where customers visit our website and browse our range of promotional products and branding options.

Our colours are black, red, white and grey.

Files must be supplied in eps, pdf and ai format.

Please display the following information:
Derek Halloway
Account Manager
Suite xxx, 212 Ferrow Lane Melbourne, Victoria 3000
Phone +61 3 5550 1827
Mobile +61 455 016 342
sales@brandvelle-example.com.au
www.brandvelle-example.com.au

```html
<!DOCTYPE html>
<html lang="en">
<head>
<meta charset="utf-8">
<title>Brandvelle Stationery</title>
<link href="https://fonts.googleapis.com/css2?family=Open+Sans:wght@400;600;700&display=swap" rel="stylesheet">
<style>
  :root{
    --red:#d0121b;
    --red-deep:#8e0a10;
    --red-mid:#b70f17;
    --grey:#6d6e71;
    --grey-light:#c9cacc;
    --charcoal:#2b2b2b;
    --white:#ffffff;
    --bg:#e8e5e1;
    --text:#3a3a3a;
  }
  *{box-sizing:border-box;margin:0;padding:0}
  html,body{width:1200px;height:1024px;overflow:hidden}
  body{background:var(--bg);font-family:"Open Sans",Arial,sans-serif;color:var(--text);position:relative}
  .piece{position:absolute;overflow:hidden;box-shadow:0 2px 6px rgba(0,0,0,.25)}
  .paper{background:var(--white)}
  .red-stock{background:radial-gradient(ellipse at 60% 55%,#e8262e 0%,var(--red-mid) 45%,var(--red-deep) 100%)}
  .swoosh{position:absolute;left:0;top:0;width:100%}
  .brand{position:absolute;display:flex;align-items:center;gap:6px;font-weight:700;letter-spacing:.5px;text-transform:uppercase;color:var(--grey)}
  .brand-dot{border-radius:50%;background:var(--red);flex:none}
  .brand.on-red{color:var(--white)}
  .brand.on-red .brand-dot{background:var(--white)}
  .contact-line{position:absolute;left:0;right:0;text-align:center;font-size:6.5px;line-height:1.45;color:var(--text)}
  .contact-line span{white-space:nowrap;margin:0 2px}
  .ico{display:inline-block;width:6px;height:6px;border-radius:50%;background:var(--red);vertical-align:-1px;margin-right:2px}
  .contact-stack{position:absolute;font-size:6.5px;line-height:1.4}
  .url{position:absolute;font-size:7.5px;color:var(--white)}
  .glow{position:absolute;border-radius:50%;background:radial-gradient(circle,rgba(255,255,255,.22) 0%,rgba(255,255,255,0) 70%)}

  /* positions */
  .letterhead-a{left:36px;top:18px;width:355px;height:500px}
  .letterhead-b{left:413px;top:18px;width:355px;height:500px}
  .folder{left:816px;top:26px;width:343px;height:486px}
  .card-front{left:46px;top:538px;width:331px;height:187px;border-radius:14px}
  .card-red-a{left:430px;top:538px;width:321px;height:187px;border-radius:14px}
  .card-red-b{left:827px;top:538px;width:321px;height:187px;border-radius:14px}
  .envelope-window{left:22px;top:740px;width:370px;height:256px}
  .envelope-back{left:413px;top:740px;width:372px;height:256px}
  .envelope-red{left:802px;top:740px;width:374px;height:256px}

  .card-name{position:absolute;left:18px;top:14px;color:var(--white);font-weight:700;font-size:13px;text-transform:uppercase}
  .card-title{position:absolute;left:18px;top:31px;color:var(--white);font-size:8px}
  .card-details{position:absolute;left:18px;top:88px;font-size:8.5px;line-height:1.3;color:var(--text)}
  .card-details .gap{height:9px}
  .address-window{position:absolute;left:24px;top:134px;width:152px;height:46px;border:1px solid #b8b8b8;border-radius:6px;background:linear-gradient(#f4f4f4,#dcdcdc)}
  .flap{position:absolute;left:0;top:0;width:100%;height:100%}
</style>
</head>
<body>

<!-- A4 letterhead, footer contacts -->
<section class="piece paper letterhead-a" aria-label="A4 letterhead">
  <svg class="swoosh" viewBox="0 0 355 80" height="80" preserveAspectRatio="none">
    <defs><linearGradient id="lhRed" x1="0" x2="1"><stop offset="0" stop-color="#9a0b12"/><stop offset=".5" stop-color="#e3202a"/><stop offset="1" stop-color="#b70f17"/></linearGradient></defs>
    <path d="M0 0H285C220 22 130 42 0 52Z" fill="url(#lhRed)"/>
    <path d="M0 56C130 46 220 26 290 2" fill="none" stroke="#2b2b2b" stroke-width="3"/>
    <path d="M0 61C130 51 225 28 300 2" fill="none" stroke="#b8b9bb" stroke-width="2"/>
  </svg>
  <div class="brand" style="right:26px;top:82px;font-size:13px">
    <span class="brand-dot" style="width:10px;height:10px"></span>Brandvelle
  </div>
  <div class="contact-line" style="bottom:18px">
    <span><i class="ico"></i>+61 3 5550 1827</span>
    <span><i class="ico"></i>+61 455 016 342</span>
    <span><i class="ico"></i>sales@brandvelle-example.com.au</span>
    <span><i class="ico"></i>www.brandvelle-example.com.au</span><br>
    Suite xxx, 212 Ferrow Lane Melbourne, Victoria 3000
  </div>
</section>

<!-- A4 letterhead, side contacts -->
<section class="piece paper letterhead-b" aria-label="A4 letterhead alternative">
  <svg class="swoosh" viewBox="0 0 355 80" height="80" preserveAspectRatio="none">
    <path d="M0 0H285C220 22 130 42 0 52Z" fill="url(#lhRed)"/>
    <path d="M0 56C130 46 220 26 290 2" fill="none" stroke="#2b2b2b" stroke-width="3"/>
    <path d="M0 61C130 51 225 28 300 2" fill="none" stroke="#b8b9bb" stroke-width="2"/>
  </svg>
  <div class="brand" style="right:26px;top:82px;font-size:13px">
    <span class="brand-dot" style="width:10px;height:10px"></span>Brandvelle
  </div>
  <div class="contact-stack" style="left:22px;top:432px">
    <div><i class="ico"></i>+61 3 5550 1827</div>
    <div><i class="ico"></i>+61 455 016 342</div>
    <div><i class="ico"></i>sales@brandvelle-example.com.au</div>
    <div>Suite xxx, 212 Ferrow Lane</div>
    <div>Melbourne, Victoria 3000</div>
  </div>
  <svg style="position:absolute;left:0;bottom:0" width="355" height="60" viewBox="0 0 355 60" preserveAspectRatio="none">
    <path d="M90 60C170 35 260 22 355 18V60Z" fill="url(#lhRed)"/>
    <path d="M80 60C170 30 260 14 355 10" fill="none" stroke="#2b2b2b" stroke-width="3"/>
    <path d="M72 60C165 25 260 8 355 4" fill="none" stroke="#b8b9bb" stroke-width="2"/>
  </svg>
  <div class="url" style="right:30px;bottom:10px">www.brandvelle-example.com.au</div>
</section>

<!-- Presentation folder -->
<section class="piece red-stock folder" aria-label="Presentation folder">
  <div class="glow" role="img" aria-label="Soft glossy highlight in brand red" style="left:60px;top:170px;width:300px;height:300px"></div>
  <div class="brand on-red" style="left:0;right:0;top:130px;justify-content:center;font-size:22px">
    <span class="brand-dot" style="width:16px;height:16px"></span>Brandvelle
  </div>
  <div class="url" style="left:0;right:0;bottom:16px;text-align:center;font-size:8px">www.brandvelle-example.com.au</div>
</section>

<!-- Business card front -->
<section class="piece paper card-front" aria-label="Business card">
  <svg class="swoosh" viewBox="0 0 331 60" height="60" preserveAspectRatio="none">
    <path d="M0 0H215C165 25 110 42 0 48Z" fill="url(#lhRed)"/>
    <path d="M0 52C110 46 170 26 220 2" fill="none" stroke="#2b2b2b" stroke-width="2.5"/>
    <path d="M0 56C115 50 175 28 228 2" fill="none" stroke="#b8b9bb" stroke-width="1.5"/>
  </svg>
  <div class="card-name">Derek Halloway</div>
  <div class="card-title">Account Manager</div>
  <div class="card-details">
    <div>Suite xxx, 212 Ferrow Lane</div>
    <div>Melbourne, Victoria 3000</div>
    <div class="gap"></div>
    <div><i class="ico"></i>+61 3 5550 1827</div>
    <div><i class="ico"></i>+61 455 016 342</div>
    <div><i class="ico"></i>sales@brandvelle-example.com.au</div>
    <div><i class="ico"></i>www.brandvelle-example.com.au</div>
  </div>
  <div class="brand" style="right:18px;top:118px;font-size:13px">
    <span class="brand-dot" style="width:10px;height:10px"></span>Brandvelle
  </div>
</section>

<!-- Business card back A -->
<section class="piece red-stock card-red-a" aria-label="Business card reverse">
  <div class="glow" role="img" aria-label="Soft glossy highlight in brand red" style="left:150px;top:10px;width:190px;height:190px"></div>
  <div class="brand on-red" style="left:16px;top:130px;font-size:14px">Brandvelle</div>
  <div class="url" style="left:28px;top:148px;font-size:7px">www.brandvelle-example.com.au</div>
</section>

<!-- Business card back B -->
<section class="piece red-stock card-red-b" aria-label="Business card reverse alternative">
  <div class="glow" role="img" aria-label="Soft glossy highlight in brand red" style="left:-10px;top:0;width:190px;height:190px"></div>
  <div class="brand on-red" style="right:18px;top:125px;font-size:14px">Brandvelle</div>
  <div class="url" style="right:30px;top:143px;font-size:7px">www.brandvelle-example.com.au</div>
</section>

<!-- DL envelope with window -->
<section class="piece paper envelope-window" aria-label="DL envelope front">
  <svg class="swoosh" viewBox="0 0 370 60" height="60" preserveAspectRatio="none">
    <path d="M0 0H290C220 22 130 36 0 40Z" fill="url(#lhRed)"/>
    <path d="M0 44C130 40 225 22 295 2" fill="none" stroke="#2b2b2b" stroke-width="3"/>
    <path d="M0 48C135 44 230 24 305 2" fill="none" stroke="#b8b9bb" stroke-width="2"/>
  </svg>
  <div class="brand" style="right:24px;top:80px;font-size:12px">
    <span class="brand-dot" style="width:9px;height:9px"></span>Brandvelle
  </div>
  <div class="address-window"></div>
  <div class="contact-line" style="bottom:16px">
    <span><i class="ico"></i>+61 3 5550 1827</span>
    <span><i class="ico"></i>+61 455 016 342</span>
    <span><i class="ico"></i>sales@brandvelle-example.com.au</span>
    <span><i class="ico"></i>www.brandvelle-example.com.au</span><br>
    Suite xxx, 212 Ferrow Lane Melbourne, Victoria 3000
  </div>
</section>

<!-- DL envelope back, white -->
<section class="piece paper envelope-back" aria-label="DL envelope back">
  <svg class="swoosh" viewBox="0 0 372 60" height="60" preserveAspectRatio="none">
    <path d="M0 0H290C220 22 130 36 0 40Z" fill="url(#lhRed)"/>
    <path d="M0 44C130 40 225 22 295 2" fill="none" stroke="#2b2b2b" stroke-width="3"/>
    <path d="M0 48C135 44 230 24 305 2" fill="none" stroke="#b8b9bb" stroke-width="2"/>
  </svg>
  <svg class="flap" viewBox="0 0 372 256" preserveAspectRatio="none">
    <path d="M0 0L186 68 372 0" fill="none" stroke="#e2e2e2" stroke-width="1"/>
  </svg>
  <div role="img" aria-label="Faint light grey and pale red background tint" style="position:absolute;left:140px;top:40px;width:240px;height:200px;border-radius:50%;background:radial-gradient(circle,rgba(240,200,190,.45) 0%,rgba(255,255,255,0) 70%)"></div>
  <div style="position:absolute;left:0;right:0;bottom:10px;text-align:center;font-size:7.5px;color:var(--text)">www.<span>brandvelle-example.com.au</span></div>
</section>

<!-- DL envelope back, red -->
<section class="piece red-stock envelope-red" aria-label="DL envelope back red">
  <svg class="flap" viewBox="0 0 374 256" preserveAspectRatio="none">
    <path d="M0 0L187 66 374 0" fill="none" stroke="rgba(0,0,0,.25)" stroke-width="1"/>
  </svg>
  <div class="glow" role="img" aria-label="Soft glossy highlight in brand red" style="left:170px;top:30px;width:220px;height:220px"></div>
  <div class="brand on-red" style="left:0;right:0;top:30px;justify-content:center;font-size:9px">
    <span class="brand-dot" style="width:8px;height:8px"></span>Brandvelle
  </div>
  <div class="url" style="left:0;right:0;bottom:10px;text-align:center;font-size:7px">www.brandvelle-example.com.au</div>
</section>

</body>
</html>
```